Anzeigengestaltung für eine Hausarztpraxis
Zielgruppe
Wir sind eine Hausarztpraxis mit zwei Standorten und suchen eine Ärztin oder einen Arzt zur Anstellung in der klassischen Hausarzt Medizin am Standort Fulenbach
Aufgabenstellung
Bitte beachtet den Text im Anhang, der ist schon vorgegeben. (Anzeigentext)
Wir suchen ein ruhiges, hochwertiges Layout für eine Stellenanzeige einer Hausarztpraxis in einem historischen Gebäude.
Der Text steht im Vordergrund, das Design soll zurückhaltend, klar und wertig sein.
Bitte keine Icons, keine bunten Farben, keine verspielten Elemente.
Gerne viel Weissraum, klare Typografie, ruhige Anmutung.
Schrift: Garamond für den Fliesstext (bereits gewählt).
Das Layout soll sowohl als PDF wie auch online funktionieren.
Optional: ein sehr dezentes grafisches Element oder eine ruhige Bildanmutung (z. B. Struktur, Licht, Architekturdetail).

```html
<!DOCTYPE html>
<html lang="de">
<head>
<meta charset="utf-8">
<title>Stellenanzeige Hausarztpraxis Fulenbach</title>
<link rel="stylesheet" href="https://fonts.googleapis.com/css2?family=EB+Garamond:ital,wght@0,400;0,600;1,400&display=swap">
<style>
  :root {
    --backdrop: #ebebed;
    --paper: #ffffff;
    --ink: #2d302c;
    --ink-strong: #1f261d;
    --accent: #2f3a2b;
    --photo-light: #ecebe6;
    --photo-wood: #8a6f57;
  }
  * { margin: 0; padding: 0; box-sizing: border-box; }
  html, body { width: 902px; height: 1200px; overflow: hidden; }
  body {
    background: var(--backdrop);
    font-family: "EB Garamond", Garamond, serif;
    color: var(--ink);
    position: relative;
  }
  .ad {
    position: absolute;
    left: 18px; top: 24px;
    width: 866px; height: 1152px;
    background: var(--paper);
  }
  .ad-photo {
    position: absolute;
    left: 448px; top: 41px;
    width: 383px; height: 207px;
    background:
      linear-gradient(180deg, var(--photo-light) 0%, #e2ded6 55%, var(--photo-wood) 100%);
  }
  .column {
    position: absolute;
    font-size: 15.5px;
    line-height: 24.4px;
  }
  .column--left { left: 38px; width: 390px; top: 176px; }
  .column--right { left: 448px; width: 380px; top: 259px; }
  .headline {
    font-weight: 600;
    font-size: 19px;
    line-height: 25px;
    color: var(--ink-strong);
    margin-bottom: 33px;
  }
  .lead { font-style: italic; }
  .column p { margin-bottom: 24.4px; }
  .section-title {
    font-weight: 600;
    font-size: 16px;
    color: var(--ink-strong);
    margin-bottom: 24.4px;
  }
  .brand {
    position: absolute;
    left: 44px; top: 1050px;
    display: flex; align-items: center; gap: 10px;
    font-size: 17px;
    font-weight: 600;
    color: var(--accent);
  }
  .brand-dot {
    width: 12px; height: 12px; border-radius: 50%;
    background: var(--accent);
  }
  .contact {
    position: absolute;
    left: 455px; top: 1018px;
    font-size: 14px;
    line-height: 19.5px;
    color: var(--ink);
  }
  .contact-email { font-weight: 600; color: var(--ink-strong); margin-bottom: 9px; }
  .contact-name { font-weight: 600; color: var(--ink-strong); }
</style>
</head>
<body>
  <article class="ad">
    <div class="ad-photo" role="img" aria-label="Heller Behandlungsraum mit Liege, Schreibtisch und Holzboden im historischen Praxisgebäude"></div>

    <section class="column column--left">
      <h1 class="headline">Hausarztmedizin mit Tiefe – dort, wo man noch echte Grundversorgung lebt</h1>
      <p class="lead">Ein Ort, der trägt. Ein Team, das bleibt. Eine Arbeit, die Wertschätzung hat.</p>
      <p>Manche Orte verändern die Art, wie man arbeitet. Unsere Praxis in Fulenbach ist so ein Ort.</p>
      <p>In einem historischen Gebäude gelegen, mit grosszügigem Ambiente, warmen Vertäfelungen und kunstvoller Wandbemalung, entstehen hier Behandlungsräume von Ruhe und Würde. Kein steriler Praxisalltag, sondern ein Ort, der Gespräche trägt und medizinische Arbeit unterstützt.</p>
      <p>Für diesen besonderen Ort suchen wir eine Hausärztin oder einen Hausarzt, die oder der nicht einfach einen Arbeitsplatz sucht, sondern einen Platz, an dem Medizin menschlich sein darf.</p>
    </section>

    <section class="column column--right">
      <h2 class="section-title">Ein Team mit Haltung</h2>
      <p>Sie arbeiten in einem freundlichen, über Jahre gewachsenen Team mit hoher personeller Kontinuität und geringer Fluktuation.</p>
      <h2 class="section-title">Zeit für gute Medizin</h2>
      <p>Unsere Patientinnen und Patienten sind überwiegend gut bis sehr gut situiert, wertschätzend und therapieoffen. Das ermöglicht ruhiges, strukturiertes Arbeiten mit Fokus auf Qualität, Beziehung und nachhaltige Behandlung.</p>
      <h2 class="section-title">Und sonst?</h2>
      <p>Der Praxisalltag ist klar strukturiert, ruhig und verlässlich. Geregelte und in Abstimmung flexible Arbeitszeiten ohne Wochenend- oder Nachtdienste, eine sehr gute leistungsbezogene Vergütung sowie ein respektvoller, wertschätzender Umgang auf Augenhöhe schaffen ein Umfeld, in dem man sich auf die medizinische Arbeit konzentrieren und langfristig wohlfühlen kann.</p>
      <p>Wir freuen uns über eine unkomplizierte Kontaktaufnahme per E-Mail oder Telefon – gerne auch ganz unverbindlich und ohne vollständige Bewerbungsunterlagen.</p>
    </section>

    <div class="brand">
      <span class="brand-dot"></span>
      <span class="brand-name">Arztpraxis Lindenhof</span>
    </div>

    <address class="contact" style="font-style: normal;">
      <div class="contact-email">E-Mail: Helga.Weißmoor@arztpraxis-lindenhof.ch</div>
      <div class="contact-name">Arztpraxis Lindenhof</div>
      <div>Brunnmattweg 7</div>
      <div>4629 Fulenbach</div>
      <div>Tel: 0629184471</div>
    </address>
  </article>
</body>
</html>
```